Fenwick Grading LTD - website for irrigation & Landscape Lighting & Buried service wire

Looking for a website to help promote my business with Irrigation (installation, service, etc) and buried service wire/drainage solutions.

Commercial/Residential

Landscape lighting.

I’ll get photos in the trucks and trailers to upload as well maybe the machine as well.

Target Market(s)

Homeowners who want green grass and beautiful gardens. Beautiful landscape lighting

Industry/Entity Type

Irrigation systems and landscape lighting and buried service wire to homes and offering Drainage soltions.

Coding

Coded - Design and coding required

Number of Pages Required

4 page

Colors
F0912C
F2A743
F7CA91
FBE8D2
FDF5EE

Requirements
Must have
• was hoping to link up my email on fenwickgrading@mailbox-example.net with the website if possible.
Nice to have
• Page for Irrigation, page for landscape lighting, page buried service wire & drainage soltions.

```html
<!DOCTYPE html>
<html lang="en">
<head>
<meta charset="utf-8">
<title>Fenwick Grading LTD</title>
<link href="https://fonts.googleapis.com/css2?family=Poppins:wght@300;400;500;600;700&display=swap" rel="stylesheet">
<style>
:root{
  --orange:#F0912C;
  --orange-2:#F2A743;
  --peach:#F7CA91;
  --cream:#FBE8D2;
  --ivory:#FDF5EE;
  --ink:#1b1b1b;
  --text:#2a2a2a;
  --grey:#7a7a7a;
  --black:#000;
  --white:#fff;
}
*{margin:0;padding:0;box-sizing:border-box}
html,body{width:1200px;height:3717px;overflow:hidden}
body{font-family:"Poppins",sans-serif;color:var(--text);background:var(--white);position:relative}
.btn{position:absolute;display:flex;align-items:center;justify-content:center;background:var(--orange);color:var(--ink);font-size:15px;box-shadow:4px 4px 0 #8d8d8d;border-left:3px solid #c9731c}

/* header */
.site-header{position:absolute;left:0;top:0;width:1200px;height:98px;background:var(--white);z-index:2}
.header-brand{position:absolute;left:0;top:0;width:318px;height:89px;background:var(--black);clip-path:polygon(0 0,270px 0,318px 89px,0 89px)}
.brand-name{color:var(--orange);font-weight:600;line-height:1.05;text-align:center}
.header-brand .brand-name{position:absolute;left:92px;top:24px;font-size:17px;letter-spacing:.5px}
.header-rule{position:absolute;left:0;top:88px;width:1200px;height:10px;background:var(--orange)}
.main-nav{position:absolute;left:410px;top:36px;display:flex;gap:23px;font-size:15px;color:#222}
.main-nav .active{font-weight:600}

/* hero */
.hero{position:absolute;left:0;top:98px;width:1200px;height:612px}
.hero-photo{position:absolute;inset:0;clip-path:polygon(0 0,1200px 0,1200px 462px,600px 588px,0 462px);background:linear-gradient(180deg,#3a4f86 0%,#c47aa8 22%,#2f3546 45%,#1d1f24 70%,#3f3a22 100%)}
.hero-line{position:absolute;left:0;top:0}
.hero-copy{position:absolute;left:0;top:230px;width:1200px;text-align:center;color:var(--white);font-size:31px;line-height:43px;letter-spacing:.5px;font-weight:400}
.hero-copy .kicker{color:var(--orange)}
.hero .btn{left:535px;top:424px;width:130px;height:38px;font-size:15px;box-shadow:none;border:none}

/* about */
.section-title{position:absolute;font-size:34px;font-weight:400;color:var(--ink)}
.section-title .hl{color:var(--orange)}
.body-copy{position:absolute;font-size:15.5px;line-height:31px;color:var(--text)}
.about-title{left:111px;top:750px}
.about-copy{left:111px;top:799px;width:470px}
.about .btn{left:114px;top:1063px;width:133px;height:46px}
.about-photo{position:absolute;left:598px;top:760px;width:436px;height:379px;clip-path:polygon(0 0,100% 0,50.7% 100%);background:linear-gradient(160deg,#dfe5ea,#6d7a86 45%,#a8b5c2 75%,#5f86b8)}

/* services */
.services-band{position:absolute;left:0;top:1237px;width:1200px;height:685px;clip-path:polygon(0 39px,1200px 0,1200px 645px,0 685px);background:linear-gradient(180deg,#dfe2dc 0%,#cdd3c4 40%,#a9b78b 75%,#98a878 100%)}
.services-title{left:0;width:1200px;top:1330px;text-align:center}
.services-sub{position:absolute;left:0;top:1380px;width:1200px;text-align:center;font-size:17px;line-height:27px;color:#222}
.card{position:absolute;top:1484px;width:289px;height:337px;border-radius:4px;overflow:hidden}
.card-1{left:111px;background:linear-gradient(180deg,#1f2a44,#3b3428 55%,#1a1a1a)}
.card-2{left:454px;background:linear-gradient(135deg,#d86a2a,#2d3a32 45%,#1e2a2a)}
.card-3{left:797px;background:linear-gradient(135deg,#5d8a3a,#c04055 40%,#2f8a55 70%,#4b5a3b)}
.card-caption{position:absolute;left:0;bottom:0;width:100%;height:90px;background:rgba(0,0,0,.78);color:var(--white);text-align:center;padding-top:14px;font-size:14px;line-height:24px}
.card-caption h3,.card-panel h3{font-size:17px;font-weight:600;line-height:24px}
.card-panel{position:absolute;left:16px;top:18px;width:256px;height:301px;background:var(--black);border-radius:6px;color:var(--white);text-align:center;padding:30px 14px 0;font-size:14px;line-height:24px}
.card-panel .btn{position:relative;display:inline-flex;margin-top:26px;width:130px;height:46px}
.arrow{position:absolute;width:28px;height:28px}

/* testimonials */
.testi-title{left:110px;top:2052px;color:var(--orange);font-size:30px;letter-spacing:1px}
.testi-copy{left:110px;top:2105px;width:470px}
.testi .btn{left:114px;top:2344px;width:133px;height:46px}
.portrait{position:absolute;left:694px;top:2039px;width:334px;height:334px;border-radius:50%;border:3px solid var(--orange);background:radial-gradient(circle at 50% 45%,#c89a7a 0%,#8c6a52 35%,#c7c0b2 70%,#e2e0da);box-shadow:0 12px 10px rgba(0,0,0,.25)}
.quote-badge{position:absolute;left:671px;top:2228px;width:92px;height:92px;border-radius:50%;background:var(--white);border:3px solid var(--orange);display:flex;align-items:center;justify-content:center;font-size:96px;font-weight:700;color:#222;line-height:1;padding-top:38px}

/* contact */
.contact{position:absolute;left:0;top:2509px;width:1200px;height:681px;background:linear-gradient(90deg,#1d2415 0%,#3a4526 35%,#7d8c54 65%,#8fa060 100%)}
.contact-item{position:absolute;left:114px;display:flex;align-items:center;gap:26px;color:var(--white);font-size:17px;line-height:30px}
.contact-icon{width:52px;height:52px;border-radius:50%;background:rgba(255,255,255,.22);display:flex;align-items:center;justify-content:center;flex:none}
.contact-card{position:absolute;left:601px;top:2578px;width:488px;height:544px;background:rgba(253,245,238,.86);border-radius:4px}
.contact-card .section-title{left:51px;top:42px;font-size:34px}
.field{position:absolute;left:53px;width:380px;border-bottom:2px solid #555;font-size:15px;color:#555;padding:0 0 6px 25px}
.contact-card .btn{left:54px;top:439px;width:131px;height:46px}

/* footer */
.site-footer{position:absolute;left:0;top:3190px;width:1200px;height:527px;background:var(--black)}
.footer-brand{position:absolute;left:115px;top:3320px;font-size:36px;line-height:1.1}
.footer-col{position:absolute;top:3270px;font-size:15.5px;line-height:34px;color:var(--white)}
.footer-col h4{font-size:15px;font-weight:600;color:var(--white)}
.social{display:flex;align-items:center;gap:16px;line-height:39px}
.social i{width:28px;height:28px;border:2px solid var(--white);border-radius:50%;display:inline-block}
.footer-rule{position:absolute;left:111px;width:978px;height:1px;background:#666}
.footer-nav{position:absolute;left:0;width:1200px;top:3540px;display:flex;justify-content:center;gap:23px;font-size:15.5px;color:var(--white)}
.footer-nav .active{font-weight:600}
.copyright{position:absolute;left:0;width:1200px;top:3645px;text-align:center;font-size:15.5px;color:var(--white)}
</style>
</head>
<body>

<header class="site-header">
  <div class="header-brand"><div class="brand-name">FENWICK<br>GRADING LTD</div></div>
  <nav class="main-nav">
    <span class="active">Home</span><span>About us</span><span>Irrigation</span><span>Service</span><span>Landscape Lighting</span><span>Fiber Optic installation</span>
  </nav>
  <div class="header-rule"></div>
</header>

<section class="hero">
  <div class="hero-photo" role="img" aria-label="Modern dark farmhouse at dusk with warm lit windows under a pink and blue sky"></div>
  <svg class="hero-line" width="1200" height="612" viewBox="0 0 1200 612">
    <polyline points="0,470 600,602 1200,470" fill="none" stroke="#6e6e6e" stroke-width="7"/>
  </svg>
  <h1 class="hero-copy"><span class="kicker">HOMEOWNERS</span><br>WHO WANT GREEN GRASS AND<br>BEAUTIFUL GARDENS. BEAUTIFUL<br>LANDSCAPE LIGHTING</h1>
  <div class="btn">Get Started</div>
</section>

<section class="about">
  <h2 class="section-title about-title"><span class="hl">About</span> Us</h2>
  <p class="body-copy about-copy">Lorem ipsum dolor sit amet, consectetur adipiscing elit, sed do eiusmod tempor incididunt ut labore et dolore magna aliqua. Ut enim ad minim veniam, quis nostrud exercitation ullamco laboris nisi ut aliquip ex ea commodo consequat. Duis aute irure dolor in reprehenderit in voluptate velit esse cillum dolore eu fugiat nulla pariatur. Excepteur sint occaecat cupidatat non proident, sunt in culpa qui officia deserunt mollit anim id est laborum.</p>
  <div class="btn">Read More</div>
  <div class="about-photo" role="img" aria-label="Technicians in hard hats installing a fiber optic junction box"></div>
</section>

<section class="services">
  <div class="services-band" role="img" aria-label="Soft-focus lawn with a sprinkler in front of a house"></div>
  <h2 class="section-title services-title"><span class="hl">Our</span> Services</h2>
  <p class="services-sub">Irrigation systems and landscape lighting and fiber optic<br>installation to homes</p>
  <svg class="arrow" style="left:60px;top:1559px" viewBox="0 0 28 28"><circle cx="14" cy="14" r="12" fill="none" stroke="#222" stroke-width="2"/><polyline points="16,8 10,14 16,20" fill="none" stroke="#222" stroke-width="2"/></svg>
  <svg class="arrow" style="left:1108px;top:1559px" viewBox="0 0 28 28"><circle cx="14" cy="14" r="12" fill="none" stroke="#222" stroke-width="2"/><polyline points="12,8 18,14 12,20" fill="none" stroke="#222" stroke-width="2"/></svg>
  <div class="card card-1" role="img" aria-label="Modern house entrance with lit landscape lighting at night">
    <div class="card-caption"><h3>Landscape Lighting</h3>Lorem ipsum dolor sit amet,<br>consectetur adipiscing elit,</div>
  </div>
  <div class="card card-2" role="img" aria-label="Fiber optic cables being installed">
    <div class="card-panel"><h3>Fiber Optic</h3>Lorem ipsum dolor sit amet, consectetur adipiscing elit, sed do eiusmod tempor incididunt ut labore et dolore magna aliqua.<br><span class="btn">Read More</span></div>
  </div>
  <div class="card card-3" role="img" aria-label="Gardener installing irrigation among flower beds">
    <div class="card-caption"><h3>irrigation installs</h3>Lorem ipsum dolor sit amet,<br>consectetur adipiscing elit,</div>
  </div>
</section>

<section class="testi">
  <h2 class="section-title testi-title">TESTIMONIALS</h2>
  <p class="body-copy testi-copy">Lorem ipsum dolor sit amet, consectetur adipiscing elit, sed do eiusmod tempor incididunt ut labore et dolore magna aliqua.Lorem ipsum dolor sit amet, consectetur adipiscing elit, sed do eiusmod tempor incididunt ut labore et dolore magna aliqua.Lorem ipsum dolor sit amet, consectetur adipiscing elit, sed do eiusmod tempor incididunt ut labore et dolore magna aliqua.</p>
  <div class="btn">Read More</div>
  <svg class="arrow" style="left:60px;top:2176px" viewBox="0 0 28 28"><circle cx="14" cy="14" r="12" fill="none" stroke="#222" stroke-width="2"/><polyline points="16,8 10,14 16,20" fill="none" stroke="#222" stroke-width="2"/></svg>
  <svg class="arrow" style="left:1108px;top:2176px" viewBox="0 0 28 28"><circle cx="14" cy="14" r="12" fill="none" stroke="#222" stroke-width="2"/><polyline points="12,8 18,14 12,20" fill="none" stroke="#222" stroke-width="2"/></svg>
  <div class="portrait" role="img" aria-label="Portrait photo of a smiling customer"></div>
  <div class="quote-badge">&#8220;</div>
</section>

<section class="contact" role="img" aria-label="Lawn sprinkler spraying water on green grass at dusk"></section>
<div class="contact-item" style="top:2740px">
  <span class="contact-icon"><svg width="24" height="24" viewBox="0 0 24 24" fill="none" stroke="#fff" stroke-width="1.6"><path d="M12 21s-6-6.5-6-11a6 6 0 0 1 12 0c0 4.5-6 11-6 11z"/><circle cx="12" cy="10" r="2.2"/></svg></span>
  <span>123 Lorem ipsum 12 st<br>123654 lorem</span>
</div>
<div class="contact-item" style="top:2821px">
  <span class="contact-icon"><svg width="24" height="24" viewBox="0 0 24 24" fill="none" stroke="#fff" stroke-width="1.6"><rect x="3" y="6" width="18" height="12"/><polyline points="3,6 12,13 21,6"/></svg></span>
  <span>fenwickgrading@mailbox-example.net</span>
</div>
<div class="contact-item" style="top:2898px">
  <span class="contact-icon"><svg width="24" height="24" viewBox="0 0 24 24" fill="none" stroke="#fff" stroke-width="1.6"><path d="M5 4h4l2 5-2.5 1.5a11 11 0 0 0 5 5L15 13l5 2v4a2 2 0 0 1-2 2A16 16 0 0 1 3 6a2 2 0 0 1 2-2z"/></svg></span>
  <span>+1 888 888 8888</span>
</div>
<form class="contact-card">
  <h2 class="section-title"><span class="hl">Contact</span> Us</h2>
  <div class="field" style="top:124px">Name</div>
  <div class="field" style="top:207px">Email</div>
  <div class="field" style="top:289px">Phone Number</div>
  <div class="field" style="top:373px">Message</div>
  <div class="btn">Submit</div>
</form>

<footer class="site-footer"></footer>
<div class="brand-name footer-brand">FENWICK<br>GRADING LTD</div>
<div class="footer-col" style="left:387px;width:190px"><h4>About Us</h4>Lorem ipsum dolor sit amet, consectetur adipiscing elit, sed do eiusmod tempor</div>
<div class="footer-col" style="left:632px"><h4>Contact Us</h4>123 Lorem ipsum 12 st<br>123654 lorem<br>fenwickgrading@mailbox-example.net<br>+1 888 888 8888</div>
<div class="footer-col" style="left:962px"><h4>Follow Us</h4>
  <div class="social"><i></i>Pinboard</div>
  <div class="social"><i></i>Photogram</div>
  <div class="social"><i></i>ChatLine</div>
  <div class="social"><i></i>VidStream</div>
</div>
<div class="footer-rule" style="top:3511px"></div>
<nav class="footer-nav"><span class="active">Home</span><span>About us</span><span>Irrigation</span><span>Service</span><span>Landscape Lighting</span><span>Fiber Optic installation</span></nav>
<div class="footer-rule" style="top:3597px"></div>
<p class="copyright">Copyright @2024 Fenwick Grading. All right Reserved</p>

</body>
</html>
```